Support People to improve their image and well-being by provided personalised advise

We need a design for business cards that could be used for production on plano press. We build a new business in our region for advising mostly women (also men though) on style embracing several aspects including fashion, style, self-confidence and ultimately your internal and external image. The business card should be "classy", "french-style". The business is located in the french -speaking part of Switzerland, close to France. The name of the company is Lomu Grace

Target Market(s)

Service fees won't be cheap (medium to premium) thus we target mid-class to upper-class women (1st target) and men (2nd target)

Industry/Entity Type

Life Coaching

Contact Information for Business Card

Conseil en Image

+41 76 418 63 07
tovasel@lomu-grace.example
profile.example/in/sel-moran-tova

Logo Text

Lomu Grace

Colors

Designer to choose colors to be used in the design.

```html
<!DOCTYPE html>
<html lang="en">
<head>
<meta charset="utf-8">
<title>Lomu Grace – Business Cards</title>
<link rel="stylesheet" href="https://fonts.googleapis.com/css2?family=Lato:wght@400;700&display=swap">
<style>
  :root {
    --bg: #3b3634;
    --card-dark: #121112;
    --card-purple: #752678;
    --accent: #b620bd;
    --white: #ffffff;
    --text-light: #e8e4ea;
    --divider-dark: #2c2a2d;
  }
  * { margin: 0; padding: 0; box-sizing: border-box; }
  html, body { width: 1200px; height: 900px; overflow: hidden; }
  body {
    background: var(--bg);
    font-family: "Lato", Arial, sans-serif;
    position: relative;
  }
  .card {
    position: absolute;
    width: 520px;
    height: 300px;
    border-radius: 3px;
  }
  .card--front {
    left: 60px; top: 320px;
    background: var(--card-dark);
  }
  .card--back {
    left: 620px; top: 200px;
    background: var(--card-purple);
  }
  .front-brand {
    position: absolute;
    left: 0; top: 0;
    width: 280px; height: 100%;
    display: flex; align-items: center; justify-content: center; gap: 12px;
  }
  .brand-mark {
    width: 16px; height: 16px;
    background: var(--accent);
    flex: none;
  }
  .brand-name {
    font-weight: 400;
    font-size: 38px;
    letter-spacing: 1px;
    color: var(--accent);
    white-space: nowrap;
  }
  .front-divider {
    position: absolute;
    left: 286px; top: 40px;
    width: 1px; height: 220px;
    background: var(--divider-dark);
  }
  .front-details {
    position: absolute;
    left: 306px; top: 78px;
    color: var(--text-light);
  }
  .person-name {
    font-weight: 700;
    font-size: 17px;
    color: var(--accent);
    letter-spacing: 0.3px;
  }
  .person-title {
    font-size: 13px;
    margin-top: 2px;
  }
  .contact-list {
    list-style: none;
    margin-top: 22px;
    font-size: 13px;
  }
  .contact-list li {
    display: flex; align-items: center; gap: 8px;
    margin-bottom: 8px;
    white-space: nowrap;
  }
  .contact-icon { width: 11px; height: 11px; flex: none; }
  .back-content {
    position: absolute;
    inset: 0;
    display: flex; flex-direction: column; align-items: center;
    padding-top: 78px;
  }
  .back-brand {
    display: flex; align-items: center; gap: 14px;
  }
  .back-brand .brand-mark { background: var(--white); width: 18px; height: 18px; }
  .back-brand .brand-name { color: var(--white); font-size: 46px; }
  .back-rule {
    position: relative;
    width: 360px; height: 1px;
    background: rgba(255,255,255,0.75);
    margin-top: 42px;
  }
  .back-rule-dot {
    position: absolute;
    left: 50%; top: 50%;
    width: 18px; height: 18px;
    margin: -9px 0 0 -9px;
    border-radius: 50%;
    background: var(--white);
  }
  .profile-link {
    margin-top: 18px;
    font-size: 15px;
    color: var(--white);
    letter-spacing: 0.3px;
  }
</style>
</head>
<body>
  <section class="card card--front" aria-label="Business card front">
    <div class="front-brand">
      <span class="brand-mark"></span>
      <span class="brand-name">Lomu Grace</span>
    </div>
    <div class="front-divider"></div>
    <div class="front-details">
      <p class="person-name">ELIAS MARCHAND</p>
      <p class="person-title">Managing Director</p>
      <ul class="contact-list">
        <li>
          <svg class="contact-icon" viewBox="0 0 12 12" aria-hidden="true">
            <path d="M2.5 1 L4.5 1 L5.2 3.5 L4 4.5 Q5 7 7.5 8 L8.5 6.8 L11 7.5 L11 9.5 Q11 11 9.5 11 Q1 10 1 2.5 Q1 1 2.5 1 Z" fill="var(--accent)"/>
          </svg>
          +41 76 418 63 07
        </li>
        <li>
          <svg class="contact-icon" viewBox="0 0 12 12" aria-hidden="true">
            <rect x="0.5" y="2" width="11" height="8" fill="var(--accent)"/>
            <path d="M0.5 2 L6 6.5 L11.5 2" fill="none" stroke="var(--card-dark)" stroke-width="1"/>
          </svg>
          tovasel@lomu-grace.example
        </li>
      </ul>
    </div>
  </section>

  <section class="card card--back" aria-label="Business card back">
    <div class="back-content">
      <div class="back-brand">
        <span class="brand-mark"></span>
        <span class="brand-name">Lomu Grace</span>
      </div>
      <div class="back-rule"><span class="back-rule-dot"></span></div>
      <p class="profile-link">profile.example/in/sel-moran-tova</p>
    </div>
  </section>
</body>
</html>
```